Wedding Videography Wordpress Website Theme

We need a modern and high-end website look for our wedding video and film business. We film weddings all over the United Kingdom and at European destinations so need something to reflect our work. The website should be visually stunning with images and videos being the focal point as this is what our services are.

The current website is www.brunolessway.com so you will be able to see our brand.

My Instagram is www.instagram.com/brunolesswayfilms so a new design should link in with this idea.

We need the following pages designed by the winning designer

1 - Homepage
2 - Films Index Page
3 - Testimonials
4 - Prices
5 - Reviews
6 - Meet Bruno (About)
7 - Contact
8 - Blog Index
9 - Blog Page

All pages must be consistent so have a similar style.

Pages on menu:
Meet Bruno
Videos
Packages
Testimionials
Journal (Blog)
Contact

We require a responsive look too. Over 90% of our visitors access the website via their mobile devices.

```html
<!DOCTYPE html>
<html lang="en">
<head>
<meta charset="utf-8">
<title>Bruno Lessway Wedding Films</title>
<link href="https://fonts.googleapis.com/css2?family=Josefin+Sans:wght@400;600;700&family=Lato:wght@400;700&family=Great+Vibes&display=swap" rel="stylesheet">
<style>
:root{
  --gold:#a38c4f;
  --gold-dark:#8d7841;
  --ink:#1d1d1d;
  --text:#444;
  --grey-band:#f4f4f4;
  --footer:#161616;
  --white:#fff;
}
*{margin:0;padding:0;box-sizing:border-box}
html,body{width:1200px;height:4264px;overflow:hidden}
body{position:relative;background:var(--white);font-family:'Lato',sans-serif;color:var(--text)}
.abs{position:absolute}
.heading{font-family:'Josefin Sans',sans-serif;color:var(--ink);font-weight:400}

/* hero */
.hero{left:0;top:0;width:1200px;height:761px;
  background:
    radial-gradient(ellipse 260px 200px at 790px 360px,rgba(235,190,150,.55),rgba(235,190,150,0) 70%),
    radial-gradient(ellipse 420px 260px at 720px 120px,rgba(150,160,190,.7),rgba(150,160,190,0) 75%),
    linear-gradient(90deg,#3e3630 0%,#6b5f55 18%,rgba(0,0,0,0) 38%,rgba(0,0,0,0) 70%,#7a6d60 84%,#4a3f36 100%),
    linear-gradient(180deg,#55667e 0%,#8a8290 22%,#8c7868 44%,#4b4139 64%,#35302c 82%,#4d4945 100%)}
.hero-shade{left:0;top:0;width:1200px;height:761px;background:linear-gradient(90deg,rgba(0,0,0,.42),rgba(0,0,0,0) 58%),linear-gradient(180deg,rgba(0,0,0,.25),rgba(0,0,0,0) 18%)}
.nav-line{left:0;top:86px;width:1200px;height:1px;background:rgba(255,255,255,.55)}
.brand{left:90px;top:72px;width:200px;text-align:center;font-family:'Josefin Sans',sans-serif;color:var(--white);font-size:14px;letter-spacing:2.5px;font-weight:600;white-space:nowrap}
.brand small{display:block;font-size:7px;letter-spacing:4px;margin-top:3px;font-weight:400}
.brand-mark{left:178px;top:30px;width:24px;height:24px;border:2px solid var(--white)}
.nav{top:40px;font-size:15px;color:var(--white);font-family:'Lato',sans-serif}
.welcome{left:109px;top:258px;font-family:'Great Vibes',cursive;color:var(--gold);font-size:38px}
.hero-title{left:109px;top:308px;font-family:'Josefin Sans',sans-serif;font-weight:700;color:var(--white);font-size:68px;letter-spacing:2px}
.hero-sub{left:110px;top:392px;font-family:'Josefin Sans',sans-serif;color:var(--white);font-size:21px}
.watch-line{left:0;top:468px;width:118px;height:1px;background:rgba(255,255,255,.8)}
.play{width:42px;height:42px;border-radius:50%;background:var(--gold);border:3px solid rgba(255,255,255,.85)}
.watch-label{left:178px;top:458px;color:var(--white);font-family:'Josefin Sans',sans-serif;font-size:16px}
.emblem{left:573px;top:734px;width:54px;height:54px;border-radius:50%;background:var(--white)}
.emblem::after{content:"";position:absolute;left:17px;top:16px;width:20px;height:20px;border:2px solid var(--gold)}

/* packages */
.section-title{font-size:35px;text-align:center;left:0;width:1200px}
.card{top:923px;width:294px;height:401px}
.card-photo{width:100%;height:100%}
.card-label{left:22px;bottom:55px;color:var(--white);font-family:'Josefin Sans',sans-serif;font-size:23px;font-weight:600}
.card-price{left:26px;bottom:28px;color:var(--white);font-size:16px;font-weight:700}
.card-feature{background:var(--gold);text-align:center;padding:54px 30px 0}
.card-feature h3{font-family:'Josefin Sans',sans-serif;color:var(--white);font-weight:400;font-size:24px;margin-bottom:18px}
.card-feature p{color:#f4eedf;font-size:14.5px;line-height:30px}
.card-feature .more{color:var(--white);font-family:'Josefin Sans',sans-serif;font-size:14px;font-weight:600;margin-top:20px;display:block}

/* intro */
.intro-band{left:0;top:1410px;width:1200px;height:579px;background:var(--grey-band)}
.intro-title{left:111px;top:1455px;font-size:34px;line-height:48px;font-weight:600}
.intro-photo{left:0;top:1617px;width:624px;height:443px;
  background:
    radial-gradient(ellipse 120px 200px at 300px 260px,rgba(240,236,228,.9),rgba(240,236,228,0) 75%),
    radial-gradient(ellipse 110px 210px at 420px 280px,rgba(80,105,160,.9),rgba(80,105,160,0) 75%),
    linear-gradient(90deg,#56683f 0%,#6f7a4e 25%,#8a6a52 38%,#c9c3b8 55%,#5b6f9a 72%,#b9bcb8 88%,#d0d2ce 100%)}
.intro-lead{left:662px;top:1454px;width:430px;font-family:'Josefin Sans',sans-serif;font-weight:600;color:var(--ink);font-size:21px;line-height:40px}
.intro-copy{left:662px;top:1586px;width:430px;font-size:14.5px;line-height:26px;color:#555}
.intro-copy p+p{margin-top:26px}
.btn{left:659px;top:1895px;width:154px;height:51px;border-radius:26px;background:var(--gold);color:var(--white);font-family:'Josefin Sans',sans-serif;font-weight:600;font-size:15px;display:flex;align-items:center;justify-content:center}

/* testimonial */
.testimonial-band{left:0;top:2966px;width:1200px;height:468px;background:radial-gradient(ellipse 500px 300px at 900px 350px,rgba(120,100,55,.35),rgba(120,100,55,0)),linear-gradient(180deg,#ab9657,#9c864a)}
.t-center{left:0;width:1200px;text-align:center;color:var(--white)}
.t-kicker{font-family:'Josefin Sans',sans-serif;font-size:21px;line-height:30px;font-weight:600}
.t-names{font-family:'Josefin Sans',sans-serif;font-size:36px}
.t-quote{left:210px;width:780px;font-size:14.5px;line-height:30px}
.t-place{font-size:15px;font-weight:700}
.video-frame{left:242px;top:3346px;width:721px;height:421px;background:var(--white);padding:7px;box-shadow:0 6px 20px rgba(0,0,0,.15)}
.video-still{width:100%;height:100%;
  background:
    radial-gradient(ellipse 110px 160px at 230px 250px,rgba(235,228,220,.9),rgba(235,228,220,0) 75%),
    radial-gradient(ellipse 120px 180px at 470px 230px,rgba(130,125,118,.9),rgba(130,125,118,0) 75%),
    linear-gradient(90deg,#3e3a36 0%,#6a625a 20%,#8c857c 45%,#5f5a55 70%,#2f2c2a 100%)}
.video-play{left:347px;top:190px;width:32px;height:32px;border-radius:50%;background:var(--gold);border:2px solid var(--white)}
.video-label{left:0;top:228px;width:707px;text-align:center;color:var(--white);font-family:'Josefin Sans',sans-serif;font-size:15px}

/* footer */
.footer{left:0;top:3850px;width:1200px;height:414px;background:var(--footer)}
.footer-brand{left:75px;top:3998px;width:320px;text-align:center;font-family:'Josefin Sans',sans-serif;color:var(--white);font-size:22px;letter-spacing:4px;font-weight:600;white-space:nowrap}
.footer-brand small{display:block;font-size:11px;letter-spacing:6px;margin-top:6px;font-weight:400}
.footer-mark{left:215px;top:3936px;width:40px;height:40px;border:2px solid var(--white)}
.social{top:4076px;width:28px;height:28px;border-radius:50%;background:var(--white)}
.social.active{background:var(--gold)}
.f-head{top:3918px;font-family:'Josefin Sans',sans-serif;color:var(--white);font-size:21px;font-weight:600}
.f-list{list-style:none;color:#ddd;font-size:14.5px;line-height:30px}
.f-list li::before{content:"«";margin-right:10px;color:#ddd}
.f-input{left:808px;top:3969px;width:278px;height:40px;border:1px solid #555;border-radius:5px;color:#888;font-size:14px;padding:11px 16px}
.f-btn{left:808px;top:4023px;width:278px;height:40px;border-radius:5px;background:var(--gold);color:var(--white);font-family:'Josefin Sans',sans-serif;font-size:15px;font-weight:600;display:flex;align-items:center;justify-content:center}
.f-rule{left:409px;top:4170px;width:791px;height:1px;background:#333}
.f-copy{left:409px;top:4204px;color:#ddd;font-size:14.5px}
</style>
</head>
<body>

<!-- hero -->
<div class="abs hero" role="img" aria-label="Dusk view of a curved city street lined with classical stone buildings"></div>
<div class="abs hero-shade"></div>
<div class="abs nav-line"></div>
<div class="abs brand-mark"></div>
<div class="abs brand">BRUNO LESSWAY<small>WEDDING FILMS</small></div>
<div class="abs nav" style="left:404px">Meet Bruno</div>
<div class="abs nav" style="left:530px">Videos</div>
<div class="abs nav" style="left:627px">Packages</div>
<div class="abs nav" style="left:745px">Testimonials</div>
<div class="abs nav" style="left:887px">Journal (Blog)</div>
<div class="abs nav" style="left:1034px">Contact</div>
<div class="abs welcome">Welcome To</div>
<div class="abs hero-title">BRUNO LESSWAY</div>
<div class="abs hero-sub">North East and Yorkshire Wedding Videographer</div>
<div class="abs watch-line"></div>
<div class="abs play" style="left:118px;top:447px"></div>
<svg class="abs" style="left:134px;top:462px" width="12" height="12" viewBox="0 0 12 12"><path d="M2 1 L11 6 L2 11 Z" fill="#fff"/></svg>
<div class="abs watch-label">Watch Video</div>
<div class="abs emblem"></div>

<!-- packages -->
<h2 class="abs heading section-title" style="top:840px">Our Packages</h2>
<div class="abs card" style="left:111px">
  <div class="card-photo" role="img" aria-label="Groom and laughing bride embracing" style="background:radial-gradient(ellipse 90px 140px at 200px 180px,rgba(225,190,160,.9),rgba(225,190,160,0) 75%),linear-gradient(100deg,#2f2b26 0%,#4a4239 40%,#8c7f70 60%,#c9b9a4 80%,#7d7262 100%)"></div>
  <div class="abs card-label">Wedding Photography</div>
  <div class="abs card-price">£700</div>
</div>
<div class="abs card card-feature" style="left:453px">
  <h3>Late Night Filming</h3>
  <p>My normal coverage ends shortly after the first dance however I am available to stay until 10pm to capture more partying and antics. This is perfect to capture more guests dancing and often many funny moments.</p>
  <span class="more">Learn More &nbsp;»</span>
</div>
<div class="abs card" style="left:794px">
  <div class="card-photo" role="img" aria-label="Close-up of hands holding, showing an engagement ring" style="background:radial-gradient(ellipse 120px 110px at 150px 170px,rgba(222,180,150,.95),rgba(222,180,150,0) 75%),linear-gradient(150deg,#7f8a5e,#a99a78 45%,#6f7452 100%)"></div>
  <div class="abs card-label">Engagement Film</div>
  <div class="abs card-price">£200</div>
</div>

<!-- intro -->
<div class="abs intro-band"></div>
<h2 class="abs heading intro-title">Your Wedding Day Is The<br>Most Important Day<br>Of Your Life...</h2>
<div class="abs intro-photo" role="img" aria-label="Bride and groom touching foreheads beside a wall with countryside behind"></div>
<div class="abs intro-lead">The celebration of your love story... and you'll want to remember it for the rest of your lives.</div>
<div class="abs intro-copy">
  <p>Your wedding film is the best way to keep this day alive forever ... a newlywed's gift that keeps giving ... an infinite reminder of those special moments and memories.</p>
  <p>Everything about your wedding day belongs to you, the couple. Your story. Your vibe. Your friends and family. Your pre-wedding jitters. Your tears. Your laughter. Your vows. Your excitement. Your first dance. Everything. And I'm passionate about creating a wedding film that captures the very essence of your day and turning it into a family heirloom you'll treasure forever.</p>
</div>
<div class="abs btn">Learn More</div>

<!-- gallery -->
<h2 class="abs heading section-title" style="top:2132px">Our Gallery</h2>
<div class="abs" role="img" aria-label="Couple holding sparklers at night" style="left:117px;top:2211px;width:312px;height:343px;background:radial-gradient(ellipse 70px 60px at 190px 170px,rgba(255,225,170,.9),rgba(255,225,170,0) 75%),radial-gradient(ellipse 80px 110px at 70px 150px,rgba(200,160,130,.75),rgba(200,160,130,0) 75%),radial-gradient(ellipse 80px 110px at 250px 90px,rgba(190,145,115,.7),rgba(190,145,115,0) 75%),linear-gradient(180deg,#1a1614,#2b231e)"></div>
<div class="abs" role="img" aria-label="Bride cuddling a small flower girl" style="left:445px;top:2211px;width:311px;height:343px;background:radial-gradient(ellipse 130px 110px at 150px 290px,rgba(240,238,236,.95),rgba(240,238,236,0) 75%),radial-gradient(ellipse 70px 80px at 170px 130px,rgba(225,195,170,.9),rgba(225,195,170,0) 75%),linear-gradient(135deg,#4a5536,#6e6a58 40%,#2e2e2c 100%)"></div>
<div class="abs" role="img" aria-label="Smiling couple walking through confetti" style="left:771px;top:2211px;width:311px;height:343px;background:radial-gradient(ellipse 90px 100px at 80px 280px,rgba(245,244,240,.95),rgba(245,244,240,0) 75%),radial-gradient(ellipse 90px 180px at 240px 250px,rgba(170,165,155,.9),rgba(170,165,155,0) 75%),linear-gradient(180deg,#c9cdca,#e7e3dc 45%,#b7b2a8)"></div>
<div class="abs" role="img" aria-label="Couple holding hands on a narrow stone street" style="left:117px;top:2567px;width:492px;height:316px;background:radial-gradient(ellipse 70px 90px at 255px 260px,rgba(240,240,245,.95),rgba(240,240,245,0) 75%),radial-gradient(ellipse 40px 120px at 320px 210px,rgba(45,45,48,.9),rgba(45,45,48,0) 75%),linear-gradient(100deg,#c8c3b8,#a39b8f 40%,#6f665c 70%,#8a8176)"></div>
<div class="abs" role="img" aria-label="Bride walking down the aisle with her father" style="left:622px;top:2567px;width:460px;height:316px;background:radial-gradient(ellipse 80px 150px at 300px 210px,rgba(230,215,200,.9),rgba(230,215,200,0) 75%),radial-gradient(ellipse 90px 170px at 80px 220px,rgba(40,45,70,.9),rgba(40,45,70,0) 75%),linear-gradient(100deg,#3a2c22,#6e5540 50%,#2c241e)"></div>

<!-- testimonial -->
<div class="abs testimonial-band"></div>
<div class="abs t-center t-kicker" style="top:3026px">North East &amp; Yorkshire Wedding Videographer<br>Video Testimonial</div>
<div class="abs t-center t-names" style="top:3100px">Amara + Leo</div>
<div class="abs t-center t-quote" style="top:3158px">“we Have A Really Emotional Video For Our Wedding. It Is A Beauty Video That Is Going To Stay With Us For The Rest Of Our Lives. Bruno Was Everywhere But You Couldn't Tell He Was There. He Was A Really Fun Guy And We Now Consider Him A Friend.”</div>
<div class="abs t-center t-place" style="top:3272px">Married At Villa Serena, Umbria, Italy</div>
<div class="abs video-frame">
  <div class="video-still" role="img" aria-label="Newlyweds walking out through a shower of confetti"></div>
  <div class="abs video-play"></div>
  <svg class="abs" style="left:359px;top:202px" width="10" height="10" viewBox="0 0 10 10"><path d="M1 0 L10 5 L1 10 Z" fill="#fff"/></svg>
  <div class="abs video-label">Watch Video</div>
</div>

<!-- footer -->
<div class="abs footer"></div>
<div class="abs footer-mark"></div>
<div class="abs footer-brand">BRUNO LESSWAY<small>WEDDING FILMS</small></div>
<div class="abs social active" style="left:160px"></div>
<div class="abs social" style="left:198px"></div>
<div class="abs social" style="left:234px"></div>
<div class="abs social" style="left:271px"></div>

<div class="abs f-head" style="left:409px">Quick Link</div>
<ul class="abs f-list" style="left:405px;top:3958px">
  <li>Meet Bruno</li><li>Videos</li><li>Packages</li><li>Testimonials</li><li>Journal (Blog)</li><li>Contact</li>
</ul>
<div class="abs f-head" style="left:594px">Help Link</div>
<ul class="abs f-list" style="left:594px;top:3958px">
  <li>Terms&amp;Conditions</li><li>Privacy Policy</li><li>About Us</li><li>Support</li>
</ul>
<div class="abs f-head" style="left:808px">Get Our Newsletter</div>
<div class="abs f-input">Enter Your Email</div>
<div class="abs f-btn">Subscribe Now</div>
<div class="abs f-rule"></div>
<div class="abs f-copy">©Copyrights 2022 Bruno Lessway | &nbsp; All Rights Reserved</div>

</body>
</html>
```